Web Calculator design Housing Investment

We have a web calculator that needs to be fixed from a design perspective. The key tasks are:<br/>1. Selecting icons / pictures / colours for the various steps<br/>2. Designing navigation between calculator steps<br/>3. Making suggestions for chart design. The limitation is that the charts are all using the Vextra API (the same charts that Vextra Grids use).<br/><br/>There are four entry screens and then a result screen. See attached PDF for screenshots. You can see our website at https://larkhollowfunds.com for our corporate colours and style.

Target Market(s)

Real Estate Investors

Industry/Entity Type

Financial Planning

Number of Pages Required

1 page

Font styles to use
Sans Serif
Other font styles liked:
• Ubuntu

Colors
86cae7
3176b5
0455a3
ffffff

Requirements
Must have
• New Icons
• Suggested design for navigation
• Suggested design for charts

```html
<!DOCTYPE html>
<html lang="en">
<head>
<meta charset="utf-8">
<title>Property Calculator — Lark Hollow Funds</title>
<link rel="stylesheet" href="https://fonts.googleapis.com/css2?family=Open+Sans:wght@400;600;700&display=swap">
<style>
:root{
  --band-a:#0a55a3;
  --band-b:#0a7ec2;
  --side:#0d2236;
  --side-active:#06131e;
  --side-line:#1b3349;
  --side-text:#c3ccd6;
  --content:#e8ecf1;
  --card:#ffffff;
  --ink:#1f2a36;
  --muted:#6f7379;
  --brand:#0a7cc0;
  --brand-dark:#0a5aa8;
  --track:#c5ccd6;
}
*{box-sizing:border-box;margin:0;padding:0}
html,body{width:881px;height:1200px;overflow:hidden}
body{font-family:"Open Sans",Arial,sans-serif;background:linear-gradient(90deg,var(--band-a),var(--band-b));color:var(--ink)}
.screen{position:relative;width:881px;height:300px}
.sidebar{position:absolute;left:7px;top:9px;width:155px;height:264px;background:var(--side)}
.nav-item{display:flex;align-items:center;height:37px;padding-left:10px;border-bottom:1px solid var(--side-line);color:var(--side-text);font-weight:700;font-size:8.5px;letter-spacing:.1px;white-space:nowrap}
.nav-item.active{background:var(--side-active);color:#fff}
.nav-item svg{width:9px;height:9px;margin-right:6px;flex:none}
.content{position:absolute;left:162px;top:9px;width:712px;height:264px;background:var(--content)}
.title{position:absolute;left:18px;top:24px;font-size:11px;font-weight:400;color:var(--ink);white-space:nowrap}
.steps{position:absolute;right:18px;top:23px;display:flex;gap:3px}
.btn{width:52px;height:18px;display:flex;align-items:center;justify-content:center;font-size:7.5px}
.btn.prev{border:1px solid #b9bec5;color:#777;background:#f4f6f8}
.btn.next{background:var(--brand);color:#fff}
.footer{position:absolute;left:0;top:273px;width:881px;height:27px;display:flex;align-items:center;justify-content:center;color:#fff;font-size:5.8px}
.card{position:absolute;background:var(--card);text-align:center}
.type-card{top:55px;width:183px;height:183px}
.type-card svg{position:absolute;left:68px;top:51px;width:48px;height:48px}
.type-label{position:absolute;top:108px;width:100%;font-size:23px;color:var(--muted)}
.type-card.selected{box-shadow:0 4px 14px rgba(0,0,0,.18)}
.type-card.selected .type-label{color:var(--brand-dark)}
.panel{position:absolute;left:18px;background:var(--card);width:674px}
.map{position:absolute;left:83px;top:13px;width:172px;height:156px;background:var(--brand);border-radius:40% 45% 40% 35%}
.slider{position:absolute;width:184px}
.slider .label{font-size:7.5px;color:var(--ink);white-space:nowrap;display:flex;align-items:center;gap:3px}
.help{display:inline-flex;align-items:center;justify-content:center;width:6px;height:6px;border-radius:50%;background:#111;color:#fff;font-size:4.5px;font-weight:700}
.slider .value{font-size:11px;font-weight:600;color:var(--brand);margin-top:1px}
.track{position:relative;height:3px;background:var(--track);margin-top:4px}
.fill{position:absolute;left:0;top:0;height:3px;background:var(--brand)}
.knob{position:absolute;top:-2px;width:7px;height:7px;border-radius:50%;background:#333}
.method{top:55px;width:220px;height:183px}
.method svg{position:absolute;left:87px;top:50px;width:46px;height:46px}
.method h3{position:absolute;top:111px;width:100%;font-size:15.5px;font-weight:400;color:var(--muted)}
.method p{position:absolute;top:137px;left:14px;right:14px;font-size:7px;line-height:10px;color:#555}
.note{position:absolute;font-size:5.9px;color:var(--ink);white-space:nowrap}
.select{position:absolute;width:73px;height:16px;border:1px solid #c9ced5;font-size:5px;color:#555;display:flex;align-items:center;padding-left:5px;background:#fff}
.select::after{content:"";position:absolute;right:6px;top:5px;width:3px;height:3px;border-right:1px solid #555;border-bottom:1px solid #555;transform:rotate(45deg)}
.chart{position:absolute;left:15px;top:40px;width:214px;height:143px;border:1px solid #e1e4e8}
.assumption{position:absolute;left:281px;top:95px;width:360px}
.assumption .label{font-size:6px;color:var(--ink);white-space:nowrap}
.assumption .value{font-size:11px;font-weight:600;color:var(--brand);margin-top:1px}
</style>
</head>
<body>

<!-- Step 1: property type -->
<section class="screen">
  <nav class="sidebar">
    <div class="nav-item active"><svg viewBox="0 0 10 10" fill="currentColor"><rect x="0" y="1" width="2" height="2"/><rect x="3" y="1" width="7" height="2"/><rect x="0" y="4" width="2" height="2"/><rect x="3" y="4" width="7" height="2"/><rect x="0" y="7" width="2" height="2"/><rect x="3" y="7" width="7" height="2"/></svg>PROPERTY TYPE</div>
    <div class="nav-item"><svg viewBox="0 0 10 10" fill="currentColor"><path d="M5 0a3.5 3.5 0 0 0-3.5 3.5C1.5 6 5 10 5 10s3.5-4 3.5-6.5A3.5 3.5 0 0 0 5 0zm0 5a1.4 1.4 0 1 1 0-2.8A1.4 1.4 0 0 1 5 5z"/></svg>PROPERTY LOCATION</div>
    <div class="nav-item"><svg viewBox="0 0 10 10" fill="none" stroke="currentColor"><rect x=".5" y=".5" width="9" height="9"/><path d="M.5 3.5h9M.5 6.5h9M3.5 3.5v6M6.5 3.5v6"/></svg>PROPERTY VALUATION</div>
    <div class="nav-item"><svg viewBox="0 0 10 10" fill="currentColor"><rect x="0" y="9" width="10" height="1"/><rect x="0" y="1" width="1" height="9"/><rect x="2" y="5" width="1.5" height="4"/><rect x="4.5" y="2" width="1.5" height="7"/><rect x="7" y="4" width="1.5" height="5"/></svg>YOUR PROPERTY PORECAST</div>
    <div class="nav-item"><svg viewBox="0 0 10 10" fill="none" stroke="currentColor"><rect x=".5" y=".5" width="9" height="9"/><path d="M.5 3.5h9M.5 6.5h9M3.5 3.5v6M6.5 3.5v6"/></svg>CALCULATION</div>
  </nav>
  <main class="content">
    <h1 class="title">What type of property would you like to compare?</h1>
    <div class="steps"><span class="btn prev">« Previous</span><span class="btn next">Next »</span></div>
    <div class="card type-card" style="left:18px">
      <svg viewBox="0 0 48 48" fill="none" stroke="#8a8d92" stroke-width="1.6"><rect x="13" y="2" width="20" height="44"/><rect x="5" y="12" width="8" height="34"/><rect x="33" y="12" width="10" height="34"/><path d="M17 8h3M26 8h3M17 15h3M26 15h3M17 22h3M26 22h3M17 29h3M26 29h3M8 18v3M8 26v3M37 18v3M37 26v3M20 46v-8h6v8"/></svg>
      <div class="type-label">Unit</div>
    </div>
    <div class="card type-card selected" style="left:218px">
      <svg viewBox="0 0 48 48" fill="none" stroke="#0a5aa8" stroke-width="1.8"><path d="M2 24 24 4l22 20M8 19v27h32V19M11 10V4h4v6"/><circle cx="24" cy="16" r="2.5"/><rect x="18" y="28" width="12" height="18"/><rect x="10" y="28" width="6" height="8"/><rect x="32" y="28" width="6" height="8"/><path d="M2 46h44"/></svg>
      <div class="type-label">House</div>
    </div>
  </main>
  <footer class="footer">Copyright © 2019 &nbsp;Lark Hollow Funds. &nbsp;All rights reserved.</footer>
</section>

<!-- Step 2: location -->
<section class="screen">
  <nav class="sidebar">
    <div class="nav-item"><svg viewBox="0 0 10 10" fill="currentColor"><rect x="0" y="1" width="2" height="2"/><rect x="3" y="1" width="7" height="2"/><rect x="0" y="4" width="2" height="2"/><rect x="3" y="4" width="7" height="2"/><rect x="0" y="7" width="2" height="2"/><rect x="3" y="7" width="7" height="2"/></svg>PROPERTY TYPE</div>
    <div class="nav-item active"><svg viewBox="0 0 10 10" fill="currentColor"><path d="M5 0a3.5 3.5 0 0 0-3.5 3.5C1.5 6 5 10 5 10s3.5-4 3.5-6.5A3.5 3.5 0 0 0 5 0zm0 5a1.4 1.4 0 1 1 0-2.8A1.4 1.4 0 0 1 5 5z"/></svg>PROPERTY LOCATION</div>
    <div class="nav-item"><svg viewBox="0 0 10 10" fill="none" stroke="currentColor"><rect x=".5" y=".5" width="9" height="9"/><path d="M.5 3.5h9M.5 6.5h9M3.5 3.5v6M6.5 3.5v6"/></svg>PROPERTY VALUATION</div>
    <div class="nav-item"><svg viewBox="0 0 10 10" fill="currentColor"><rect x="0" y="9" width="10" height="1"/><rect x="0" y="1" width="1" height="9"/><rect x="2" y="5" width="1.5" height="4"/><rect x="4.5" y="2" width="1.5" height="7"/><rect x="7" y="4" width="1.5" height="5"/></svg>YOUR PROPERTY PORECAST</div>
    <div class="nav-item"><svg viewBox="0 0 10 10" fill="none" stroke="currentColor"><rect x=".5" y=".5" width="9" height="9"/><path d="M.5 3.5h9M.5 6.5h9M3.5 3.5v6M6.5 3.5v6"/></svg>CALCULATION</div>
  </nav>
  <main class="content">
    <h1 class="title">Where would this property be lcoated?</h1>
    <div class="steps"><span class="btn prev">« Previous</span><span class="btn next">Next »</span></div>
    <div class="panel" style="top:55px;height:183px">
      <div class="map" role="img" aria-label="Map of Australia with a location pin"></div>
      <div class="slider" style="left:414px;top:41px">
        <div class="label">How much will the property cost? <span class="help">?</span></div>
        <div class="value">$500,000</div>
        <div class="track"><div class="fill" style="width:55px"></div><div class="knob" style="left:52px"></div></div>
      </div>
      <div class="slider" style="left:414px;top:111px">
        <div class="label">How much will you invest? <span class="help">?</span></div>
        <div class="value">$200,000</div>
        <div class="track"><div class="fill" style="width:26px"></div><div class="knob" style="left:22px"></div></div>
      </div>
    </div>
  </main>
  <footer class="footer">Copyright © 2019 &nbsp;Lark Hollow Funds. &nbsp;All rights reserved.</footer>
</section>

<!-- Step 3: valuation -->
<section class="screen">
  <nav class="sidebar">
    <div class="nav-item"><svg viewBox="0 0 10 10" fill="currentColor"><rect x="0" y="1" width="2" height="2"/><rect x="3" y="1" width="7" height="2"/><rect x="0" y="4" width="2" height="2"/><rect x="3" y="4" width="7" height="2"/><rect x="0" y="7" width="2" height="2"/><rect x="3" y="7" width="7" height="2"/></svg>PROPERTY TYPE</div>
    <div class="nav-item"><svg viewBox="0 0 10 10" fill="currentColor"><path d="M5 0a3.5 3.5 0 0 0-3.5 3.5C1.5 6 5 10 5 10s3.5-4 3.5-6.5A3.5 3.5 0 0 0 5 0zm0 5a1.4 1.4 0 1 1 0-2.8A1.4 1.4 0 0 1 5 5z"/></svg>PROPERTY LOCATION</div>
    <div class="nav-item active"><svg viewBox="0 0 10 10" fill="none" stroke="currentColor"><rect x=".5" y=".5" width="9" height="9"/><path d="M.5 3.5h9M.5 6.5h9M3.5 3.5v6M6.5 3.5v6"/></svg>PROPERTY VALUATION</div>
    <div class="nav-item"><svg viewBox="0 0 10 10" fill="currentColor"><rect x="0" y="9" width="10" height="1"/><rect x="0" y="1" width="1" height="9"/><rect x="2" y="5" width="1.5" height="4"/><rect x="4.5" y="2" width="1.5" height="7"/><rect x="7" y="4" width="1.5" height="5"/></svg>YOUR PROPERTY PORECAST</div>
    <div class="nav-item"><svg viewBox="0 0 10 10" fill="none" stroke="currentColor"><rect x=".5" y=".5" width="9" height="9"/><path d="M.5 3.5h9M.5 6.5h9M3.5 3.5v6M6.5 3.5v6"/></svg>CALCULATION</div>
  </nav>
  <main class="content">
    <h1 class="title">How would you like to forecast the returns from property?</h1>
    <div class="steps"><span class="btn prev">« Previous</span><span class="btn next">Next »</span></div>
    <div class="card method" style="left:18px">
      <svg viewBox="0 0 46 46" fill="none" stroke="#8a8d92" stroke-width="1.6"><path d="M23 2v38M6 10h34M14 44h18M18 40h10"/><circle cx="23" cy="4" r="2"/><path d="M10 10 3 25h14zM36 10l-7 15h14zM3 25a7 4 0 0 0 14 0M29 25a7 4 0 0 0 14 0"/></svg>
      <h3>Relative Cost</h3>
      <p>Use this to value property based on mortgage cost relative to rent cost</p>
    </div>
    <div class="card method" style="left:245px">
      <svg viewBox="0 0 46 46" fill="none" stroke="#8a8d92" stroke-width="1.6"><rect x="24" y="2" width="19" height="42"/><path d="M18 8l8-3M16 14l8-2"/><circle cx="34" cy="23" r="4"/><rect x="2" y="28" width="7" height="16"/><path d="M9 30h8l7-4h5M9 42h22l6-4M20 34h11"/></svg>
      <h3>Relative to Wages</h3>
      <p>Use this to value property based on mortgage cost relative to wages</p>
    </div>
    <div class="card method" style="left:472px">
      <svg viewBox="0 0 46 46" fill="none" stroke="#8a8d92" stroke-width="1.6"><path d="M26 6h14v14L18 42 4 28z"/><circle cx="34" cy="12" r="2.5"/><path d="M35 11l8-9"/></svg>
      <h3>Using Rental Yield</h3>
      <p>Use this to value property based on a rental yield</p>
    </div>
  </main>
  <footer class="footer">Copyright © 2019 &nbsp;Lark Hollow Funds. &nbsp;All rights reserved.</footer>
</section>

<!-- Step 4: forecast -->
<section class="screen">
  <nav class="sidebar">
    <div class="nav-item"><svg viewBox="0 0 10 10" fill="currentColor"><rect x="0" y="1" width="2" height="2"/><rect x="3" y="1" width="7" height="2"/><rect x="0" y="4" width="2" height="2"/><rect x="3" y="4" width="7" height="2"/><rect x="0" y="7" width="2" height="2"/><rect x="3" y="7" width="7" height="2"/></svg>PROPERTY TYPE</div>
    <div class="nav-item"><svg viewBox="0 0 10 10" fill="currentColor"><path d="M5 0a3.5 3.5 0 0 0-3.5 3.5C1.5 6 5 10 5 10s3.5-4 3.5-6.5A3.5 3.5 0 0 0 5 0zm0 5a1.4 1.4 0 1 1 0-2.8A1.4 1.4 0 0 1 5 5z"/></svg>PROPERTY LOCATION</div>
    <div class="nav-item"><svg viewBox="0 0 10 10" fill="none" stroke="currentColor"><rect x=".5" y=".5" width="9" height="9"/><path d="M.5 3.5h9M.5 6.5h9M3.5 3.5v6M6.5 3.5v6"/></svg>PROPERTY VALUATION</div>
    <div class="nav-item active"><svg viewBox="0 0 10 10" fill="currentColor"><rect x="0" y="9" width="10" height="1"/><rect x="0" y="1" width="1" height="9"/><rect x="2" y="5" width="1.5" height="4"/><rect x="4.5" y="2" width="1.5" height="7"/><rect x="7" y="4" width="1.5" height="5"/></svg>YOUR PROPERTY PORECAST</div>
    <div class="nav-item"><svg viewBox="0 0 10 10" fill="none" stroke="currentColor"><rect x=".5" y=".5" width="9" height="9"/><path d="M.5 3.5h9M.5 6.5h9M3.5 3.5v6M6.5 3.5v6"/></svg>CALCULATION</div>
  </nav>
  <main class="content">
    <h1 class="title" style="top:15px">Your property price forecast</h1>
    <div class="steps" style="top:13px"><span class="btn prev">« Previous</span><span class="btn next">Next »</span></div>
    <div class="panel" style="top:44px;height:198px">
      <div class="note" style="left:15px;top:13px">You have chosen to forecast property price using</div>
      <div class="select" style="left:171px;top:10px">Gross Rental Yield</div>
      <div class="note" style="left:281px;top:13px">You can see how this ratio has changed over time (in blue) below vs your assumption (in red ) for</div>
      <div class="select" style="left:585px;top:10px">Sydney House</div>
      <svg class="chart" viewBox="0 0 400 268" font-family="Open Sans, sans-serif" font-size="7" fill="#555">
        <g stroke="#eee"><path d="M33 16h346M33 61h346M33 106h346M33 151h346M33 196h346"/></g>
        <text x="14" y="19">5000</text><text x="14" y="64">4000</text><text x="14" y="109">3000</text><text x="14" y="154">2000</text><text x="14" y="199">1000</text><text x="26" y="244">0</text>
        <path d="M33 173.5 64.5 169 95.9 187 127.4 155.5 158.8 162.3 190.3 133 221.7 146.5 253.2 124 284.6 83.5 316.1 56.5 347.5 40.8 379 25V241H33z" fill="#d4e6f5"/>
        <path d="M33 220.8 64.5 225.3 95.9 223 127.4 227.5 158.8 216.3 190.3 202.8 221.7 189.3 253.2 196 284.6 182.5 316.1 178 347.5 169 379 160V241H33z" fill="#b6c5d3"/>
        <polyline points="33,173.5 64.5,169 95.9,187 127.4,155.5 158.8,162.3 190.3,133 221.7,146.5 253.2,124 284.6,83.5 316.1,56.5 347.5,40.8 379,25" fill="none" stroke="#5aa6dc" stroke-width="1.5"/>
        <polyline points="33,220.8 64.5,225.3 95.9,223 127.4,227.5 158.8,216.3 190.3,202.8 221.7,189.3 253.2,196 284.6,182.5 316.1,178 347.5,169 379,160" fill="none" stroke="#222" stroke-width="1.5"/>
        <g fill="#fff" stroke="#5aa6dc" stroke-width="1.3"><circle cx="33" cy="173.5" r="3.5"/><circle cx="64.5" cy="169" r="3.5"/><circle cx="95.9" cy="187" r="3.5"/><circle cx="127.4" cy="155.5" r="3.5"/><circle cx="158.8" cy="162.3" r="3.5"/><circle cx="190.3" cy="133" r="3.5"/><circle cx="221.7" cy="146.5" r="3.5"/><circle cx="253.2" cy="124" r="3.5"/><circle cx="284.6" cy="83.5" r="3.5"/><circle cx="316.1" cy="56.5" r="3.5"/><circle cx="347.5" cy="40.8" r="3.5"/><circle cx="379" cy="25" r="3.5"/></g>
        <g fill="#fff" stroke="#222" stroke-width="1.3"><circle cx="33" cy="220.8" r="3.5"/><circle cx="64.5" cy="225.3" r="3.5"/><circle cx="95.9" cy="223" r="3.5"/><circle cx="127.4" cy="227.5" r="3.5"/><circle cx="158.8" cy="216.3" r="3.5"/><circle cx="190.3" cy="202.8" r="3.5"/><circle cx="221.7" cy="189.3" r="3.5"/><circle cx="253.2" cy="196" r="3.5"/><circle cx="284.6" cy="182.5" r="3.5"/><circle cx="316.1" cy="178" r="3.5"/><circle cx="347.5" cy="169" r="3.5"/><circle cx="379" cy="160" r="3.5"/></g>
        <rect x="162" y="98" width="64" height="15" fill="#1d1d1d"/><text x="167" y="108" fill="#fff" font-size="7">$ 2400 in June</text>
        <rect x="46" y="25" width="6" height="6" fill="#5aa6dc"/><text x="55" y="31">Earnings</text>
        <rect x="46" y="34" width="6" height="6" fill="#222"/><text x="55" y="40">Sales</text>
        <g font-size="6.5" text-anchor="middle"><text x="33" y="254">Jan</text><text x="64.5" y="254">Feb</text><text x="95.9" y="254">Mar</text><text x="127.4" y="254">Apr</text><text x="158.8" y="254">May</text><text x="190.3" y="254">Jun</text><text x="221.7" y="254">Jul</text><text x="253.2" y="254">Aug</text><text x="284.6" y="254">Sep</text><text x="316.1" y="254">Oct</text><text x="347.5" y="254">Nov</text><text x="379" y="254">Dec</text></g>
      </svg>
      <div class="assumption">
        <div class="label">By default we assume the ration stays at the latest value of 3.4%. You can change this assumption using the slider.</div>
        <div class="value">3.4%</div>
        <div class="track" style="width:184px"><div class="fill" style="width:52px"></div><div class="knob" style="left:51px"></div></div>
      </div>
    </div>
  </main>
  <footer class="footer">Copyright © 2019 &nbsp;Lark Hollow Funds. &nbsp;All rights reserved.</footer>
</section>

</body>
</html>
```